Property management company looking for modern card design

We at Blue Heron Partners provides property management services for its residential and commercial properties, with expertise in all categories of multifamily, industrial and office projects throughout California.

We need a business card design that is professional and modern designed business card. In our field, clients get hundreds of business cards, we would like our card to stand out.

Please avoid small print.

Target Market(s)

Professionals and high end clients

Industry/Entity Type

Financial Planning

Contact Information for Business Card

Company Name: Blue Heron Partners, Name, email, license #, phone number, website blueheronpartners.com

Font styles to use
Sans Serif

Requirements
Must have
• The card design needs to be adaptable because there is a possibly we will be expanding into different sectors other than real estate. The card design should be focused on financial planning and asset management.
Nice to have
• Modern and simple business card. Eye catching. Non-standard size/shaped cards would be great.
• blueheronpartners.com
Should not have
• Too many bright color or any pictures or shapes of real estate stuff.

```html
<!DOCTYPE html>
<html lang="en">
<head>
<meta charset="utf-8">
<title>Blue Heron Partners – Business Card</title>
<link href="https://fonts.googleapis.com/css2?family=Montserrat:wght@300;400;600&display=swap" rel="stylesheet">
<style>
  :root {
    --backdrop: #e8e5e1;
    --card: #333333;
    --accent: #d0393a;
    --ink: #ffffff;
    --muted: #d9d9d9;
    --rule: #8a8a8a;
  }
  * { margin: 0; padding: 0; box-sizing: border-box; }
  html, body {
    width: 1200px; height: 1000px; overflow: hidden;
    background: var(--backdrop);
    font-family: "Montserrat", sans-serif;
  }
  .stage { position: relative; width: 1200px; height: 1000px; }
  .card {
    position: absolute; left: 288px; width: 626px; height: 357px;
    background: var(--card); border-radius: 22px;
    box-shadow: 0 6px 14px rgba(0,0,0,0.25);
  }
  .card--front { top: 140px; }
  .card--back { top: 532px; }

  .wordmark {
    position: absolute; left: 0; right: 0; top: 140px;
    text-align: center; color: var(--ink);
    font-weight: 400; font-size: 34px; letter-spacing: 1px;
  }
  .wordmark-rule {
    position: absolute; left: 122px; width: 382px; top: 213px;
    height: 1px; background: var(--rule);
  }

  .emblem {
    position: absolute; left: 86px; top: 88px;
    width: 180px; height: 180px; border-radius: 50%;
    background: var(--accent);
  }
  .divider {
    position: absolute; left: 296px; top: 108px; width: 1px; height: 140px;
    background: linear-gradient(to bottom, transparent, #777 30%, #777 70%, transparent);
  }
  .details { position: absolute; left: 327px; top: 99px; color: var(--ink); }
  .person-name { color: var(--accent); font-weight: 600; font-size: 21px; line-height: 26px; }
  .person-title { font-size: 14px; font-weight: 400; line-height: 18px; }
  .license { margin-top: 14px; font-size: 14px; font-weight: 400; }
  .license-label { color: var(--accent); font-weight: 300; }
  .contact-list { list-style: none; margin-top: 14px; }
  .contact-item {
    display: flex; align-items: center; gap: 8px;
    font-size: 14px; font-weight: 400; line-height: 22.5px; color: var(--ink);
  }
  .contact-icon { width: 12px; height: 12px; flex: none; }
</style>
</head>
<body>
<main class="stage">
  <section class="card card--front">
    <h1 class="wordmark">BLUE HERON PARTNERS</h1>
    <div class="wordmark-rule"></div>
  </section>

  <section class="card card--back">
    <div class="emblem"></div>
    <div class="divider"></div>
    <div class="details">
      <p class="person-name">Daniel Reyes</p>
      <p class="person-title">President</p>
      <p class="license"><span class="license-label">License:</span> #7318460</p>
      <ul class="contact-list">
        <li class="contact-item">
          <svg class="contact-icon" viewBox="0 0 24 24" fill="none" stroke="#d0393a" stroke-width="2.4"><path d="M5 3h4l2 5-2.5 1.5a11 11 0 0 0 6 6L16 13l5 2v4a2 2 0 0 1-2 2A17 17 0 0 1 3 5a2 2 0 0 1 2-2z"/></svg>
          555-0142-7730
        </li>
        <li class="contact-item">
          <svg class="contact-icon" viewBox="0 0 24 24"><rect x="2" y="5" width="20" height="14" rx="1" fill="#d0393a"/><path d="M2 6l10 7 10-7" fill="none" stroke="#333" stroke-width="2"/></svg>
          info@blueheronpartners.com
        </li>
        <li class="contact-item">
          <svg class="contact-icon" viewBox="0 0 24 24" fill="none" stroke="#d0393a" stroke-width="2"><circle cx="12" cy="12" r="10"/><path d="M2 12h20M12 2c3 3 3 17 0 20M12 2c-3 3-3 17 0 20"/></svg>
          www.blueheronpartners.com
        </li>
      </ul>
    </div>
  </section>
</main>
</body>
</html>
```